Thistlewick Superfoods Packaging Design

We are looking for a design for our premium superfoods powders and blends. Packaging dimensions are 21cm x 13cm Kraft packaging (light brown background). This design should be a blueprint for other products that we will be marketing including lions mane mushroom, reishi mushroom, Chaga mushroom, Spirilina, bee pollen, açai powder and the like. The design should be clean but earthy, and the template replicable for other products.

```html
<!DOCTYPE html>
<html lang="en">
<head>
<meta charset="utf-8">
<title>Thistlewick Superfoods – Reishi Mushroom Pouch Label</title>
<link href="https://fonts.googleapis.com/css2?family=Questrial&family=Open+Sans:wght@400;600&family=Crimson+Text:ital@1&display=swap" rel="stylesheet">
<style>
  :root {
    --kraft: #c4a47d;
    --mint: #c9ede5;
    --mint-light: #d8f5ee;
    --label-white: #f4f5f4;
    --ink: #1c1c1c;
    --rule: #6d7f7b;
    --badge-green: #5d9b3a;
    --badge-soft: #8dbb5c;
    --illustration: #5b5b5b;
  }
  * { margin: 0; padding: 0; box-sizing: border-box; }
  html, body { width: 941px; height: 1200px; overflow: hidden; }
  body { background: var(--kraft); position: relative; font-family: "Open Sans", sans-serif; color: var(--ink); }

  .label {
    position: absolute; left: 132px; top: 36px; width: 677px; height: 1127px;
    background: var(--label-white);
  }
  .label__panel {
    position: absolute; left: 0; top: 0; width: 677px; height: 888px;
    background: linear-gradient(180deg, var(--mint-light) 0%, var(--mint) 60%, var(--mint) 100%);
  }
  .cert-tab {
    position: absolute; left: 403px; top: 0; width: 198px; height: 69px;
    background: var(--label-white); border-radius: 0 0 10px 10px;
    display: flex; align-items: center; justify-content: center; gap: 8px;
  }
  .cert-tab .badge { width: 36px; height: 36px; border-radius: 50%; background: var(--badge-green); }
  .cert-tab .badge--soft { background: var(--badge-soft); }
  .cert-tab .badge--square { border-radius: 4px; background: none; border: 2px solid var(--badge-soft); }

  .product-title {
    position: absolute; right: 78px; top: 88px; text-align: right;
    font-family: "Questrial", sans-serif; font-weight: 400; font-size: 92px; line-height: 87px;
    letter-spacing: -1px; color: var(--ink);
  }
  .intro {
    position: absolute; right: 78px; top: 279px; text-align: right; z-index: 2;
    font-size: 12.5px; line-height: 20px; text-transform: uppercase; color: var(--ink);
    white-space: nowrap; letter-spacing: -0.2px;
  }
  .illustration {
    position: absolute; left: 5px; top: 300px; width: 340px; height: 370px;
    border-radius: 50%;
    background: radial-gradient(ellipse at 45% 45%, #8a8a8a 0%, var(--illustration) 55%, #2f2f2f 100%);
    opacity: 0.85; z-index: 1;
  }
  .nutrition { position: absolute; left: 449px; top: 452px; list-style: none; }
  .nutrition li { display: flex; align-items: center; height: 43px; }
  .nutrition .factor { font-size: 27px; width: 48px; font-weight: 400; }
  .nutrition .compare { font-size: 12px; line-height: 15px; font-weight: 600; text-transform: uppercase; }

  .rule { position: absolute; left: 79px; width: 513px; height: 1px; background: var(--rule); z-index: 0; }
  .rule--top { top: 662px; }
  .rule--bottom { top: 832px; }

  .description {
    position: absolute; left: 79px; top: 686px; width: 513px;
    font-family: "Crimson Text", serif; font-style: italic; font-size: 15px; line-height: 26px;
    color: #2a2a2a;
  }
  .description span { display: block; text-align: justify; text-align-last: justify; white-space: nowrap; }
  .description span.last { text-align-last: left; }
  .net-weight { position: absolute; right: 85px; top: 848px; font-size: 14px; }

  .brand {
    position: absolute; left: 0; top: 965px; width: 677px;
    display: flex; flex-direction: column; align-items: center;
  }
  .brand__row { display: flex; align-items: center; gap: 10px; }
  .brand__dot { width: 14px; height: 14px; border-radius: 50%; background: var(--badge-green); }
  .brand__name { font-family: "Questrial", sans-serif; font-size: 30px; color: var(--ink); }
  .brand__rule { width: 216px; height: 1px; background: var(--ink); margin-top: 14px; }
</style>
</head>
<body>
  <section class="label">
    <div class="label__panel">
      <div class="cert-tab">
        <span class="badge"></span>
        <span class="badge badge--soft"></span>
        <span class="badge badge--square"></span>
        <span class="badge"></span>
      </div>

      <h1 class="product-title">REISHI<br>MUSHROOM</h1>

      <p class="intro">Moringa, also known as ‘the miracle<br>tree’, has been praised for it’s<br>health benefits for thousands<br>of years. It is extremely rich in<br>healthy antioxidants and<br>bioactive compounds. If<br>fact it has:</p>

      <div class="illustration" role="img" aria-label="Engraved ink illustration of a reishi mushroom cap and stem"></div>

      <ul class="nutrition">
        <li><span class="factor">7x</span><span class="compare">The vitamin C<br>of oranges</span></li>
        <li><span class="factor">4x</span><span class="compare">The calcium<br>of milk</span></li>
        <li><span class="factor">3x</span><span class="compare">The potassium<br>of bananas</span></li>
        <li><span class="factor">3x</span><span class="compare">Iron<br>of spinich</span></li>
      </ul>

      <div class="rule rule--top"></div>
      <p class="description">
        <span>The leaves contain all nine essential amino acids and traditionally used in</span>
        <span>assisting the healing of many ailments. The nutiritional diveristy is also known</span>
        <span>to reduce both cholesterol and blood sugar levels whilst and have serious</span>
        <span>anti-inflammatory benefits. Our 100% organic moringa is grown and harvested</span>
        <span class="last">in it’s native enviornment, supporting premium superfood nutrition.</span>
      </p>
      <div class="rule rule--bottom"></div>
      <span class="net-weight">250g</span>
    </div>

    <div class="brand">
      <div class="brand__row">
        <span class="brand__name">Thistlewick Superfoods</span>
        <span class="brand__dot"></span>
      </div>
      <div class="brand__rule"></div>
    </div>
  </section>
</body>
</html>
```